Business Card Design

I am an Event and Wedding Planner in need of an eye catching business card featuring my logo (attached), my contact details, and my company tagline (Making every celebration glow with wonder...) I would like the tagline in font similar the logo's font.
Updates
I have just noticed that my logo has a misspelling so for the final design, I will be uploading a corrected logo as soon as I have it.
My apologies.
Reason: Waiting on a corrected logo...Lantern is misspelled and it should say Weddings not Wedding
The logo has been corrected so now Lantern is spelled correctly and it says Weddings instead of Wedding. Please use Edwardian Script ITC as the font for the tagline so it will match the logo. Thank you for your patience.
Target Market(s)
Engaged couples and people hosting milestone celebrations. 25-50 years old, predominately female
Industry/Entity Type
Business
Contact Information for Business Card
Rosalind Merrow, Event Manager / Owner, Mobile: 0491 868 254, Email: rosalind@velvetlanternco.com.au, www.velvetlanternco.com.au, Making every celebration glow with wonder...

```html
<!DOCTYPE html>
<html lang="en">
<head>
<meta charset="utf-8">
<title>Velvet Lantern – Business Card</title>
<link rel="stylesheet" href="https://fonts.googleapis.com/css2?family=Pinyon+Script&family=Arimo:wght@400&family=Tinos:ital@1&display=swap">
<style>
  :root {
    --backdrop: #e4e4e4;
    --paper: #ffffff;
    --ink: #1e1e1e;
    --brand-red: #c21f2a;
    --faint-ink: #d2d2d2;
    --heart-grey: #9c9c9c;
    --card-shadow: 0 6px 14px rgba(0,0,0,0.28);
  }
  html, body {
    margin: 0;
    width: 1200px;
    height: 1000px;
    overflow: hidden;
    background: var(--backdrop);
  }
  .canvas { position: relative; width: 1200px; height: 1000px; }

  .card {
    position: absolute;
    width: 725px;
    height: 430px;
    background: var(--paper);
    box-shadow: var(--card-shadow);
    overflow: hidden;
  }
  .card--front { left: 100px; top: 55px; }
  .card--back  { left: 330px; top: 500px; }

  .side-band {
    position: absolute;
    top: 0; bottom: 0; right: 0;
    background: var(--brand-red);
  }
  .card--front .side-band { left: 503px; }
  .card--back  .side-band { left: 490px; }
  .side-band__stripe {
    position: absolute; top: 0; bottom: 0;
    background: var(--paper);
  }
  .side-band__stripe--inner { left: 6px; width: 5px; }
  .side-band__stripe--outer { left: 34px; width: 6px; }

  .heart-pair {
    position: absolute;
    width: 80px; height: 70px;
    background: var(--heart-grey);
    border: 4px solid var(--ink);
    border-radius: 30px 30px 14px 30px;
    box-sizing: border-box;
  }
  .card--front .heart-pair { left: 618px; top: 338px; }
  .card--back  .heart-pair { left: 615px; top: 330px; }

  /* brand name in the card's text face */
  .brand-name {
    position: absolute;
    margin: 0;
    display: flex;
    align-items: center;
    justify-content: center;
    font-family: "Arimo", sans-serif;
    font-weight: 400;
    color: var(--ink);
    text-align: center;
  }
  .card--front .brand-name {
    left: 75px; top: 70px; width: 340px; height: 240px;
    font-size: 40px;
  }
  .brand-name--faint { color: var(--faint-ink); }
  .card--back .brand-name {
    left: 205px; top: 30px; width: 235px; height: 160px;
    font-size: 28px;
  }

  .tagline {
    position: absolute;
    left: 22px; top: 366px;
    margin: 0;
    font-family: "Pinyon Script", cursive;
    font-size: 28px;
    color: var(--brand-red);
  }

  .holder { position: absolute; left: 13px; top: 14px; color: var(--brand-red); }
  .holder__name {
    margin: 0;
    font-family: "Arimo", sans-serif;
    font-size: 17px;
    letter-spacing: 0.3px;
    text-transform: uppercase;
  }
  .holder__role {
    margin: 1px 0 0;
    font-family: "Tinos", serif;
    font-style: italic;
    font-size: 15px;
  }

  .contact-list {
    position: absolute;
    left: 36px; top: 228px;
    margin: 0; padding: 0;
    list-style: none;
  }
  .contact-list__item {
    display: flex; align-items: center;
    height: 29px;
    font-family: "Arimo", sans-serif;
    font-size: 18px;
    color: var(--brand-red);
  }
  .contact-list__icon { width: 24px; height: 22px; margin-right: 16px; flex: none; }
</style>
</head>
<body>
<main class="canvas">

  <section class="card card--front" aria-label="Card front">
    <p class="brand-name">Velvet Lantern</p>
    <p class="tagline">Making every celebration glow with wonder...</p>
    <div class="side-band">
      <span class="side-band__stripe side-band__stripe--inner"></span>
      <span class="side-band__stripe side-band__stripe--outer"></span>
    </div>
    <div class="heart-pair" role="img" aria-label="Pair of grey hearts ornament"></div>
  </section>

  <section class="card card--back" aria-label="Card back">
    <div class="holder">
      <p class="holder__name">Rosalind Merrow</p>
      <p class="holder__role">Event Manager / Owner</p>
    </div>
    <p class="brand-name brand-name--faint" aria-hidden="true">Velvet Lantern</p>
    <ul class="contact-list">
      <li class="contact-list__item">
        <svg class="contact-list__icon" viewBox="0 0 24 22" aria-hidden="true">
          <rect x="1" y="3" width="22" height="16" fill="var(--brand-red)"/>
          <polyline points="1,3 12,12 23,3" fill="none" stroke="#fff" stroke-width="1.6"/>
        </svg>
        rosalind@velvetlanternco.com.au
      </li>
      <li class="contact-list__item">
        <svg class="contact-list__icon" viewBox="0 0 24 22" aria-hidden="true">
          <path d="M2 7 Q12 1 22 7 L20 10 L16 8 L16 6 Q12 5 8 6 L8 8 L4 10 Z" fill="var(--brand-red)"/>
          <path d="M6 10 L18 10 L21 20 L3 20 Z" fill="var(--brand-red)"/>
          <circle cx="12" cy="15" r="2.6" fill="#fff"/>
        </svg>
        0491 868 254
      </li>
      <li class="contact-list__item">
        <svg class="contact-list__icon" viewBox="0 0 24 22" aria-hidden="true">
          <g fill="none" stroke="var(--brand-red)" stroke-width="1.5">
            <circle cx="12" cy="11" r="9.5"/>
            <ellipse cx="12" cy="11" rx="4.5" ry="9.5"/>
            <line x1="2.5" y1="11" x2="21.5" y2="11"/>
            <line x1="12" y1="1.5" x2="12" y2="20.5"/>
          </g>
        </svg>
        www.velvetlanternco.com.au
      </li>
    </ul>
    <div class="side-band">
      <span class="side-band__stripe side-band__stripe--inner"></span>
      <span class="side-band__stripe side-band__stripe--outer"></span>
    </div>
    <div class="heart-pair" role="img" aria-label="Pair of grey hearts ornament"></div>
  </section>

</main>
</body>
</html>
```